Velura Nocturna

Website for a night club with live music and cabaret dancers. I would like to have the following Menu: 1.) Home; 2) The Facilities; 3) The Show; 4) Other Attractions; 5) Videos & Fotos; 6) Program; 7) Reservations; 8) Membership; 9) Contacts.

The pages should be easily editable and allow to enter text, including the menu since the final version will be in both English and Portuguese. It should have a toggle or links for the Portuguese language and the English Language.

The night club itself is called "VELURA NOCTURNA"; and its URL is www.veluranocturna.example.

```html
<!DOCTYPE html>
<html lang="en">
<head>
<meta charset="utf-8">
<title>Velura Nocturna</title>
<link href="https://fonts.googleapis.com/css2?family=Acme&family=Fira+Sans:ital,wght@0,300;0,400;0,500;1,300&display=swap" rel="stylesheet">
<style>
:root{
  --coral:#f06b6b;
  --dark:#242424;
  --darker:#151515;
  --panel:#2b2b2b;
  --light:#f7f7f7;
  --yellow:#f5d000;
  --text:#555;
  --white:#fff;
  --fb:#3b5b9a;
  --tw:#5bc4ea;
  --clip:#9a9a9a;
}
*{margin:0;padding:0;box-sizing:border-box}
html,body{width:691px;height:1200px;overflow:hidden}
body{position:relative;font-family:"Fira Sans",sans-serif;background:var(--white);color:var(--text)}
.abs{position:absolute}

.site-header{left:0;top:0;width:691px;height:68px;background:var(--dark)}
.brand{left:77px;top:24px;font-family:"Acme",sans-serif;font-size:20px;color:var(--coral)}
.lang{left:539px;top:34px;width:75px;height:18px;border:1px solid #777;background:#2e2e2e;color:#ccc;font-size:7px;display:flex;align-items:center;padding-left:7px;gap:6px}
.lang .flag{width:8px;height:6px;background:#c44}
.lang .caret{margin-left:auto;margin-right:7px;color:#888;font-size:6px}

.main-nav{left:0;top:68px;width:691px;height:29px;background:var(--darker)}
.main-nav a{color:#ddd;text-decoration:none;font-size:8.2px;font-weight:400;position:absolute;top:10px}
.main-nav a.active{left:76px;top:0;width:54px;height:29px;background:var(--coral);color:var(--white);font-weight:500;display:flex;align-items:center;justify-content:center}

.hero{left:0;top:97px;width:691px;height:275px;
  background:
    radial-gradient(ellipse 40px 30px at 145px 35px,rgba(225,220,60,.85),transparent),
    radial-gradient(ellipse 40px 30px at 225px 40px,rgba(225,220,60,.85),transparent),
    radial-gradient(ellipse 40px 30px at 295px 40px,rgba(225,220,60,.85),transparent),
    radial-gradient(ellipse 40px 30px at 365px 35px,rgba(225,220,60,.85),transparent),
    radial-gradient(ellipse 160px 50px at 255px 55px,rgba(210,50,50,.55),transparent),
    radial-gradient(ellipse 150px 60px at 255px 150px,rgba(150,190,90,.6),transparent),
    radial-gradient(ellipse 160px 90px at 255px 230px,rgba(140,85,55,.8),transparent),
    linear-gradient(90deg,#2a2320 0%,#3a2e28 15%,#2a2320 55%,#8f8a86 58%,#bdbab7 75%,#d2d0ce 100%);}
.hero-text{right:125px;top:109px;text-align:right}
.hero-text h1{font-family:"Acme",sans-serif;font-weight:400;font-size:18px;line-height:24px;color:#222}
.hero-text p{margin-top:14px;font-size:8.8px;line-height:17.5px;color:var(--white);font-weight:500}
.slide-arrow{top:177px;width:29px;height:29px;border-radius:50%;background:rgba(90,90,90,.75)}

.welcome{left:0;top:372px;width:691px;height:248px;background:var(--light)}
.welcome-photo{left:76px;top:50px;width:214px;height:151px;
  background:
    linear-gradient(180deg,transparent 0%,transparent 55%,rgba(40,60,30,.9) 75%,#2e2a26 100%),
    repeating-linear-gradient(90deg,#8a9aa4 0 18px,#6f7f88 18px 20px),
    linear-gradient(180deg,#c4ccd2 0%,#9aa5ab 100%);
  background-blend-mode:normal,multiply,normal}
.welcome-body{left:310px;top:48px;width:305px}
.welcome-body .pre{font-size:16px;color:#333}
.welcome-body h2{font-weight:300;font-size:21px;color:#666;margin-top:4px;letter-spacing:.2px}
.welcome-body h2 span{font-weight:400;font-size:16px;color:#333}
.welcome-body p{margin-top:12px;font-size:7.3px;line-height:13.7px;color:#666}
.btn{background:var(--yellow);color:#333;font-size:9.5px;display:flex;align-items:center;justify-content:center;text-transform:uppercase}
.welcome .btn{left:314px;top:178px;width:107px;height:23px}

.share-tab{left:0;width:15px;height:52px;border-radius:0 3px 3px 0;overflow:hidden}
.share-tab i{position:absolute;left:4px;top:4px;width:7px;height:7px;background:rgba(255,255,255,.9)}
.share-tab span{position:absolute;left:50%;top:31px;transform:translate(-50%,-50%) rotate(-90deg);font-size:7.5px;font-weight:500;color:var(--white);white-space:nowrap}

.videos{left:0;top:620px;width:691px;height:276px;background:var(--panel)}
.video-brand{left:78px;top:23px;font-size:20px;color:#ddd;font-weight:500}
.video-divider{left:155px;top:20px;width:1px;height:34px;background:#555}
.videos h3{left:169px;top:21px;font-weight:400;font-size:11.5px;color:var(--white)}
.videos .subtitle{left:169px;top:39px;font-size:9.6px;color:var(--coral)}
.video-main{left:77px;top:78px;width:309px;height:164px;
  background:
    radial-gradient(ellipse 60px 45px at 55px 70px,rgba(190,40,40,.8),transparent),
    radial-gradient(ellipse 60px 45px at 265px 120px,rgba(170,200,60,.7),transparent),
    radial-gradient(ellipse 70px 40px at 150px 30px,rgba(110,80,150,.8),transparent),
    radial-gradient(ellipse 70px 50px at 175px 125px,rgba(220,200,170,.6),transparent),
    linear-gradient(135deg,#2a2230 0%,#3a2a30 50%,#1e1c24 100%)}
.play{position:absolute;border:2px solid var(--white);border-radius:50%}
.video-thumb{left:402px;width:91px;height:61px}
.video-item{left:506px;width:110px}
.video-item h4{font-weight:400;font-size:9.6px;color:var(--coral)}
.video-item p{margin-top:6px;font-size:7.2px;line-height:10.5px;color:#ccc}
.video-item .more{margin-top:3px;font-size:6.6px;color:var(--white);letter-spacing:.4px}
.videos .btn{left:508px;top:234px;width:107px;height:22px}

.photos{left:0;top:896px;width:691px;height:206px;background:var(--white)}
.photos h2{left:74px;top:37px;font-weight:300;font-size:19.5px;color:#333}
.round-arrow{top:40px;width:14px;height:14px;border-radius:50%;background:#777}
.photo{top:74px;width:127px;height:94px;border:1px solid #ddd;padding:2px;background:var(--white);box-shadow:0 1px 2px rgba(0,0,0,.12)}
.photo div{width:100%;height:100%}

.site-footer{left:0;top:1102px;width:691px;height:98px;background:var(--dark)}
.follow{left:78px;top:26px;font-size:7px;color:#888;display:flex;align-items:center;gap:8px}
.follow i{display:inline-block;width:10px;height:10px;border-radius:2px;background:#aaa}
.copyright{left:77px;top:55px;font-size:7px;color:#aaa}
.newsletter h3{left:443px;top:19px;font-weight:400;font-size:9.6px;color:var(--white)}
.newsletter .field{left:445px;top:41px;width:166px;height:18px;background:var(--white);font-size:6.8px;font-style:italic;color:#999;padding:5px 9px}
.newsletter .btn{left:548px;top:63px;width:63px;height:18px;font-size:7.4px}
</style>
</head>
<body>

<header class="abs site-header">
  <div class="abs brand">Velura Nocturna</div>
  <div class="abs lang"><span class="flag"></span>English<span class="caret">▼</span></div>
</header>

<nav class="abs main-nav">
  <a class="active" href="#">Home</a>
  <a href="#" style="left:144px">The Facilities</a>
  <a href="#" style="left:210px">The Show</a>
  <a href="#" style="left:263px">Other Attractions</a>
  <a href="#" style="left:343px">Videos &amp; Fotos</a>
  <a href="#" style="left:413px">Program</a>
  <a href="#" style="left:455px">Reservations</a>
  <a href="#" style="left:518px">Membership</a>
  <a href="#" style="left:577px">Contacts</a>
</nav>

<section class="abs hero" role="img" aria-label="Four cabaret dancers in feathered headdresses and colourful costumes">
  <div class="abs slide-arrow" style="left:54px">
    <svg width="29" height="29" viewBox="0 0 29 29"><path d="M16.5 9l-5.5 5.5 5.5 5.5" fill="none" stroke="#fff" stroke-width="1.5"/></svg>
  </div>
  <div class="abs hero-text">
    <h1>View Cabaret Dancers<br>Latest Shows</h1>
    <p>Neque porro quisquam est qui dolorem<br>ipsum quia dolor sit amet, consectetur,<br>adipisci velit.</p>
  </div>
  <div class="abs slide-arrow" style="left:612px">
    <svg width="29" height="29" viewBox="0 0 29 29"><path d="M12.5 9l5.5 5.5-5.5 5.5" fill="none" stroke="#fff" stroke-width="1.5"/></svg>
  </div>
</section>

<section class="abs welcome">
  <div class="abs welcome-photo" role="img" aria-label="Glass-fronted club building with palm trees"></div>
  <div class="abs welcome-body">
    <div class="pre">Welcome to</div>
    <h2>VELURA NOCTURNA <span>site</span></h2>
    <p>Sed ut perspiciatis unde omnis iste natus error sit voluptatem accusantium doloremque laudantium, totam rem aperiam, eaque ipsa quae ab illo inventore veritatis et quasi architecto beatae vitae dicta sunt explicabo. Sed ut perspiciatis unde omnis iste natus error sit voluptatem accusantium doloremque laudantium, totam.</p>
  </div>
  <div class="abs btn">Find out more</div>
</section>

<div class="abs share-tab" style="top:408px;background:var(--fb)"><i></i><span>Like</span></div>
<div class="abs share-tab" style="top:472px;background:var(--tw)"><i></i><span>Follow</span></div>
<div class="abs share-tab" style="top:536px;background:var(--clip)"><i></i><span>Watch</span></div>

<section class="abs videos">
  <div class="abs video-brand">ClipReel</div>
  <div class="abs video-divider"></div>
  <h3 class="abs">FEATURED VIDEO'S</h3>
  <div class="abs subtitle">EXCEPTEUR SINT---“OCCAECAT CUPIDATAT NON PROIDENT”-(IN CULPA QUI OFFICIA)</div>

  <div class="abs video-main" role="img" aria-label="Video still of cabaret dancers on stage">
    <div class="play" style="left:135px;top:63px;width:38px;height:38px">
      <svg width="34" height="34" viewBox="0 0 34 34"><path d="M13 10l11 7-11 7z" fill="#fff"/></svg>
    </div>
  </div>

  <div class="abs video-thumb" style="top:78px;background:radial-gradient(ellipse 30px 22px at 40px 30px,rgba(200,140,90,.8),transparent),linear-gradient(135deg,#1e3a20,#2a2a1e)" role="img" aria-label="Video still of a dancer">
    <div class="play" style="left:33px;top:18px;width:26px;height:26px">
      <svg width="22" height="22" viewBox="0 0 22 22"><path d="M8 6l8 5-8 5z" fill="#fff"/></svg>
    </div>
  </div>
  <div class="abs video-item" style="top:83px">
    <h4>NEQUE PORRO</h4>
    <p>Check out this video of our soundcheck.</p>
    <div class="more">[ MORE ]</div>
  </div>

  <div class="abs video-thumb" style="top:159px;background:radial-gradient(ellipse 22px 20px at 20px 20px,rgba(170,200,60,.8),transparent),radial-gradient(ellipse 25px 22px at 75px 40px,rgba(200,60,60,.7),transparent),linear-gradient(135deg,#2a3a22,#3a2a24)" role="img" aria-label="Video still of dancers in costume">
    <div class="play" style="left:33px;top:18px;width:26px;height:26px">
      <svg width="22" height="22" viewBox="0 0 22 22"><path d="M8 6l8 5-8 5z" fill="#fff"/></svg>
    </div>
  </div>
  <div class="abs video-item" style="top:164px">
    <h4>AT VERO EOS ET</h4>
    <p>Check out this video of our soundcheck.</p>
    <div class="more">[ MORE ]</div>
  </div>

  <div class="abs btn">Find out more</div>
</section>

<section class="abs photos">
  <h2 class="abs">VIEW PHOTOS</h2>
  <div class="abs round-arrow" style="left:582px">
    <svg width="14" height="14" viewBox="0 0 14 14"><path d="M8 4l-3 3 3 3" fill="none" stroke="#fff" stroke-width="1.5"/></svg>
  </div>
  <div class="abs round-arrow" style="left:599px">
    <svg width="14" height="14" viewBox="0 0 14 14"><path d="M6 4l3 3-3 3" fill="none" stroke="#fff" stroke-width="1.5"/></svg>
  </div>
  <div class="abs photo" style="left:74px"><div role="img" aria-label="Feathered dancer performing for an audience" style="background:radial-gradient(ellipse 25px 30px at 60px 35px,rgba(160,210,200,.7),transparent),linear-gradient(180deg,#3a2a2c 0%,#5a2a2e 60%,#2a1a1c 100%)"></div></div>
  <div class="abs photo" style="left:212px"><div role="img" aria-label="Dancer in a green and red headdress" style="background:radial-gradient(ellipse 35px 20px at 60px 15px,rgba(130,200,60,.85),transparent),radial-gradient(ellipse 30px 25px at 60px 55px,rgba(200,130,90,.7),transparent),linear-gradient(135deg,#4a4a3a,#2a3a4a)"></div></div>
  <div class="abs photo" style="left:350px"><div role="img" aria-label="Dancers with purple and orange feathers" style="background:radial-gradient(ellipse 35px 30px at 45px 55px,rgba(160,60,170,.85),transparent),radial-gradient(ellipse 30px 25px at 95px 55px,rgba(220,140,40,.8),transparent),linear-gradient(135deg,#7a1a24,#3a1420)"></div></div>
  <div class="abs photo" style="left:488px"><div role="img" aria-label="Dancers silhouetted in blue stage light" style="background:radial-gradient(circle at 50% 35%,#8a9ae0,#2e3a9a 40%,#141a5a 70%,#0a0e2a)"></div></div>
</section>

<footer class="abs site-footer">
  <div class="abs follow">Follow Us : <i></i><i></i><i></i><i></i></div>
  <div class="abs copyright">Copyright © 2014 Nightframe . All right reserved.</div>
  <div class="newsletter">
    <h3 class="abs">OUR NEWSLETTER</h3>
    <div class="abs field">Enter your Email...</div>
    <div class="abs btn">Subscribe</div>
  </div>
</footer>

</body>
</html>
```